Melvane Home Page

I want to design a new home page using the look of two pages that I like.
http://us.trossini-example.com/
http://www.vellmont-example.us/?cm_mmc=seeker-_-EG_BR_Vellmont_Exact_VLM_D-_-Search-_-vellmonthttp://us.trossini-example.com/
I like the framing of the trossini site and the drop down feel of the vellmont site. I will provide a new logo later today but for now can use what is already on my home page. The pictures in the middle of the page will rotate but I like the fonts and framing from Trossini.
My current site is www.melvane-example.com and I had a designer do a file which came close but missed the mark attached. This upscale and elegant
I liek the top log but would want the glass tilted to look liek the rest of the letters and in a grey or silver elegant color.
Target Market(s)
High end individuals andn corporations

```html
<!DOCTYPE html>
<html lang="en">
<head>
<meta charset="utf-8">
<title>Melvane — Home</title>
<link rel="stylesheet" href="https://fonts.googleapis.com/css2?family=Old+Standard+TT:wght@400;700&display=swap">
<style>
  :root {
    --ink: #ffffff;
    --ink-soft: #c9c2b8;
    --ink-muted: #a39a8e;
    --header-shade: rgba(20, 12, 6, 0.55);
    --nav-shade: rgba(25, 16, 8, 0.5);
    --rule: rgba(255, 255, 255, 0.45);
    --footer-bg: #070707;
    --button-fill: #9c8568;
    --button-edge: #e8dccb;
  }
  * { margin: 0; padding: 0; box-sizing: border-box; }
  html, body { width: 1200px; height: 900px; overflow: hidden; background: #000; }
  body { font-family: "Old Standard TT", "Times New Roman", serif; color: var(--ink); }
  .page { position: relative; width: 1200px; height: 900px; overflow: hidden; }

  .hero-photo {
    position: absolute; left: 0; top: 0; width: 1200px; height: 732px;
    background:
      radial-gradient(ellipse at 30% 55%, rgba(200,150,150,0.35), transparent 45%),
      radial-gradient(ellipse at 75% 75%, rgba(235,205,150,0.55), transparent 50%),
      linear-gradient(180deg, #3a2410 0%, #6b4420 30%, #8a5a2c 50%, #a87a48 70%, #7a5030 100%);
  }

  .masthead {
    position: absolute; left: 0; top: 0; width: 1200px; height: 135px;
    background: var(--header-shade);
  }
  .brand {
    position: absolute; left: 42px; top: 40px;
    font-size: 52px; letter-spacing: 1px; line-height: 1; font-weight: 400;
  }
  .masthead-divider {
    position: absolute; left: 335px; top: 28px; width: 1px; height: 77px; background: var(--rule);
  }
  .account-links {
    position: absolute; left: 356px; top: 31px; list-style: none;
    font-size: 14.5px; letter-spacing: 0.6px; line-height: 26px;
  }
  .social-links { position: absolute; right: 2px; top: 14px; list-style: none; }
  .social-links li { width: 19px; height: 19px; margin-bottom: 3px; background: #6e6a66; }

  .main-nav {
    position: absolute; left: 0; top: 135px; width: 1200px; height: 38px;
    background: var(--nav-shade); border-top: 1px solid rgba(255,255,255,0.15);
  }
  .main-nav ul { list-style: none; display: flex; padding-left: 42px; height: 100%; align-items: center; }
  .main-nav li { font-size: 14.5px; letter-spacing: 0.5px; color: var(--ink-muted); margin-right: 50px; }
  .main-nav li.is-active { color: var(--ink); font-weight: 700; }

  .tagline {
    position: absolute; left: 66px; top: 600px;
    font-size: 57px; line-height: 52px; font-weight: 400;
  }
  .events-button {
    position: absolute; left: 795px; top: 638px; width: 353px; height: 60px;
    border-radius: 30px; background: linear-gradient(180deg, #a99175, var(--button-fill));
    border: 2px solid rgba(255,255,255,0.5);
    box-shadow: inset 0 0 0 3px rgba(0,0,0,0.15);
    display: flex; align-items: center; justify-content: center;
    font-size: 36px; color: var(--ink); text-decoration: none;
  }
  .events-button::after {
    content: ""; position: absolute; inset: 4px; border-radius: 26px;
    border: 1px dashed var(--button-edge); opacity: 0.7;
  }

  .site-footer {
    position: absolute; left: 0; top: 732px; width: 1200px; height: 168px;
    background: radial-gradient(ellipse at 50% 40%, #1a1a1a, var(--footer-bg) 70%);
    text-align: center;
  }
  .services-list {
    position: absolute; left: 0; right: 0; top: 36px; padding-left: 0;
    font-size: 19px; line-height: 24px; letter-spacing: 0.3px;
  }
  .copyright { position: absolute; left: 0; right: 0; top: 129px; font-size: 16px; padding-left: 76px; }
</style>
</head>
<body>
<div class="page">
  <div class="hero-photo" role="img" aria-label="Photograph of an elegant banquet hall set for a conference: draped tent ceiling, stage with armchairs and lectern, long tables with white-covered chairs"></div>

  <header class="masthead">
    <div class="brand">MELVANE</div>
    <div class="masthead-divider"></div>
    <ul class="account-links">
      <li>MEMBER LOGIN</li>
      <li>JOIN OUR ENTOURAGE</li>
      <li>CONTACT US</li>
    </ul>
    <ul class="social-links" aria-label="Social links">
      <li></li><li></li><li></li>
    </ul>
  </header>

  <nav class="main-nav">
    <ul>
      <li>ENTOURAGE &amp; STAFFING</li>
      <li>EVENTS</li>
      <li>TRAVEL</li>
      <li class="is-active">CELEBRITY &amp; PR</li>
      <li>OTHER SERVICES</li>
      <li>CLIENTS</li>
    </ul>
  </nav>

  <h1 class="tagline">Access the best<br>that life has to offer.</h1>
  <a class="events-button" href="#">View our events</a>

  <footer class="site-footer" role="contentinfo">
    <p class="services-list">GRAND OPENINGS, TOURISM, RESORTS, RESTAURANTS, CHARITIES,<br>CORPORATE FUNCTIONS, PRIVATE EVENTS,</p>
    <p class="copyright">Copyright © Melvane LLC 2014.</p>
  </footer>
</div>
</body>
</html>
```